Brochure for Healthy Restaurant Concept

Please design a brochure for our meal prep menu . Include all items and all descriptions of the items . Include some photos. Please ensure you let us know what size paper your design will need to be printed on. Please make it a clean modern design, matching our logo and its ok to use other colors as well. We are open to designs. We dont want it to be too plain.

Include all items including the pre-built options, bundles, and custom meals on the brochure. I will include the old brochure to give you an example, don't copy items and prices from that particular brochure as they could be inaccurate for the "Pre-Built items and breakfast items now.

Industry/Entity Type

Restaurant

Requirements
Must have
• Logo, all menu items
Nice to have
• A QR code linking our website www.ploverbarn.example

```html
<!DOCTYPE html>
<html lang="en">
<head>
<meta charset="utf-8">
<title>Plover Barn Menu Brochure</title>
<link href="https://fonts.googleapis.com/css2?family=Courier+Prime&family=Mulish:wght@300;400;500;600;700;800&display=swap" rel="stylesheet">
<style>
:root{
  --bg:#e4e4e4;
  --green:#8cc63f;
  --green-dark:#7ab52d;
  --ink:#222;
  --muted:#8a8a8a;
  --white:#fff;
}
*{box-sizing:border-box;margin:0;padding:0}
html,body{width:1200px;height:461px;overflow:hidden;background:var(--bg);font-family:'Mulish',sans-serif;color:var(--ink)}
.page{position:absolute;top:44px;width:266px;height:376px;background:var(--white);box-shadow:0 2px 6px rgba(0,0,0,.18);overflow:hidden}
.cover{left:41px}
.menu-intro{left:326px}
.menu-sides{left:611px}
.back{left:895px;top:39px;height:377px}
.photo{position:absolute;left:0;width:100%}
.cover .photo.main{top:0;height:294px;background:radial-gradient(circle at 50% 55%,#c79a5c 0%,#8a5a2c 35%,#4f6a2d 65%,#c9c3b6 100%)}
.cover .photo.strip,.back .photo.strip{bottom:0;height:9px;background:linear-gradient(90deg,#b9b3a8,#7a8f55,#c9c2b3)}
.brand{position:absolute;top:315px;width:100%;text-align:center}
.brand-name{font-weight:800;font-size:23px;color:var(--green);letter-spacing:.5px;line-height:1}
.brand-tag{margin-top:3px;font-weight:700;font-size:8px;color:var(--green);letter-spacing:.1px}
.intro-box{position:absolute;left:3px;top:2px;width:261px;height:152px;background:var(--green);color:var(--white);text-align:center}
.intro-box .kicker{position:absolute;top:19px;width:100%;font-size:7.2px;font-weight:400;letter-spacing:.2px}
.intro-box h1{position:absolute;top:29px;width:100%;font-size:9.6px;font-weight:500}
.intro-box p{position:absolute;left:22px;top:44px;width:212px;font-size:6.8px;line-height:8.95px;font-weight:400;text-align:justify}
.dot{position:absolute;border-radius:50%;background:rgba(255,255,255,.28)}
.band{position:absolute;left:3px;width:261px;height:20px;background:var(--green);color:var(--white);font-weight:700;font-size:9.3px;text-align:center;line-height:20px;letter-spacing:.2px}
.card{position:absolute;width:77px;height:56px;background:var(--white);border-radius:3px;box-shadow:0 1px 3px rgba(0,0,0,.22);overflow:hidden}
.card .shot{height:37px;background:linear-gradient(180deg,#b59a7c,#2a2a2a 60%,#8d7356)}
.card .name{position:absolute;left:4px;top:40px;font-size:6px;font-weight:500;white-space:nowrap;letter-spacing:-.1px}
.card .size{position:absolute;left:4px;top:49px;font-size:3.8px;color:var(--muted)}
.card .price{position:absolute;right:3px;top:41px;font-size:7.4px;font-weight:400;color:var(--green-dark)}
.c1{left:11px}.c2{left:93px}.c3{left:176px}
.back .photo.main{top:0;height:294px;background:radial-gradient(circle at 60% 75%,#e2a36a 0%,#b7b08f 40%,#6f9a3a 70%,#cfd6d4 100%)}
.addr{position:absolute;top:312px;font-size:7px;line-height:8.4px;color:var(--muted);white-space:nowrap}
.addr.a1{left:26px}.addr.a2{left:140px}
.social{position:absolute;top:349px;display:flex;align-items:center;gap:4px;font-family:'Courier Prime',monospace;font-size:6.4px;color:#666;white-space:nowrap}
.social .mark{width:10px;height:10px;border-radius:2px;background:#d7475e;flex:none}
.social.fb .mark{background:#3b64b0}
.social.ig{left:9px}.social.fb{left:100px}
</style>
</head>
<body>

<section class="page cover">
  <div class="photo main" role="img" aria-label="Bowl of roasted sweet potato, beets, spinach, wheat berries, green beans and zucchini"></div>
  <div class="brand">
    <div class="brand-name">PLOVER BARN</div>
    <div class="brand-tag">HEALTHY KITCHEN &nbsp;|&nbsp; MEAL PREP</div>
  </div>
  <div class="photo strip" role="img" aria-label="Table surface with fork"></div>
</section>

<section class="page menu-intro">
  <div class="intro-box">
    <span class="dot" style="left:228px;top:11px;width:21px;height:21px"></span>
    <span class="dot" style="left:239px;top:129px;width:16px;height:16px"></span>
    <div class="kicker">OUR BEST PICKS</div>
    <h1>Our Menu</h1>
    <p>Freshness, quality , nutrition profile, and flavour are just a few words to describe what goes into our menu choices here at Plover Barn Kitchen. We have a variety of items on our menu to ensure that when you stop by, you can be sure to find an item that fits your lifestyle. Everyone has different goals , and you'll see how our menu reflects that. The flavour of our dishes is what will surprise you the most. We have worked long and hard to provide the best quality , along with the best flavour profiles to have you leaving our store satisfied and planning to come back for dinner. Finally , a restaurant you can visit twice (or more) per day and not feel guilty!</p>
  </div>
  <div class="band" style="top:154px">PROTEIN BUNDLES</div>

  <div class="card c1" style="top:183px"><div class="shot" role="img" aria-label="Tray of sliced chicken"></div><span class="name">CHIKEN</span><span class="size">16OZ</span><span class="price">$18</span></div>
  <div class="card c2" style="top:183px"><div class="shot" role="img" aria-label="Tray of ground turkey"></div><span class="name">GROUND TURKEY</span><span class="size">16OZ</span><span class="price">$18</span></div>
  <div class="card c3" style="top:183px"><div class="shot" role="img" aria-label="Tray of ground beef"></div><span class="name">GROUND BEEF</span><span class="size">16OZ</span><span class="price">$16</span></div>
  <div class="card c1" style="top:245px"><div class="shot" role="img" aria-label="Tray of turkey meatballs"></div><span class="name">TURKEY MEATBALL</span><span class="size">16OZ</span><span class="price">$18</span></div>
  <div class="card c2" style="top:245px"><div class="shot" role="img" aria-label="Tray of steak bites"></div><span class="name">STEAK BITES</span><span class="size">16OZ</span><span class="price">$27</span></div>
  <div class="card c3" style="top:245px"><div class="shot" role="img" aria-label="Tray of herbed cod"></div><span class="name">COD</span><span class="size">16OZ</span><span class="price">$23</span></div>
  <div class="card c1" style="top:307px"><div class="shot" role="img" aria-label="Tray of salmon fillets"></div><span class="name">FRESH SALMON</span><span class="size">16OZ</span><span class="price">$24</span></div>
  <div class="card c2" style="top:307px"><div class="shot" role="img" aria-label="Tray of ground bison"></div><span class="name">BISON</span><span class="size">16OZ</span><span class="price">$24</span></div>
</section>

<section class="page menu-sides">
  <div class="band" style="top:3px">VEGGIE BUNDLES</div>
  <div class="card c1" style="top:28px"><div class="shot" role="img" aria-label="Tray of broccoli"></div><span class="name">BROCCOLI</span><span class="size">16OZ</span><span class="price">$9</span></div>
  <div class="card c2" style="top:28px"><div class="shot" role="img" aria-label="Tray of cauliflower"></div><span class="name">CAULIFLOWER</span><span class="size">16OZ</span><span class="price">$9.50</span></div>
  <div class="card c3" style="top:28px"><div class="shot" role="img" aria-label="Tray of carrots and peas"></div><span class="name">CARROTS &amp; PEAS</span><span class="size">16OZ</span><span class="price">$6.50</span></div>
  <div class="card c1" style="top:91px"><div class="shot" role="img" aria-label="Tray of mixed vegetables"></div><span class="name">MIXID VEGGIES</span><span class="size">16OZ</span><span class="price">$12</span></div>
  <div class="card c2" style="top:91px"><div class="shot" role="img" aria-label="Tray of mixed peppers"></div><span class="name">MIXED PEPPERS</span><span class="size">16OZ</span><span class="price">$10.50</span></div>
  <div class="card c3" style="top:91px"><div class="shot" role="img" aria-label="Tray of roasted root vegetables"></div><span class="name">ROOT MEDLEY</span><span class="size">16OZ</span><span class="price">$10.50</span></div>

  <div class="band" style="top:154px">CARB BUNDLES</div>
  <div class="card c1" style="top:182px"><div class="shot" role="img" aria-label="Tray of sweet potato mash"></div><span class="name">SWEET POTETO MASH</span><span class="size">16OZ</span><span class="price">$9</span></div>
  <div class="card c2" style="top:182px"><div class="shot" role="img" aria-label="Tray of mashed potato"></div><span class="name">MASHED POTETO</span><span class="size">16OZ</span><span class="price">$9</span></div>
  <div class="card c3" style="top:182px"><div class="shot" role="img" aria-label="Tray of baby potatoes"></div><span class="name">BABY POTETOES</span><span class="size">16OZ</span><span class="price">$9</span></div>
  <div class="card c1" style="top:244px"><div class="shot" role="img" aria-label="Tray of brown rice"></div><span class="name">BROWN RICE</span><span class="size">16OZ</span><span class="price">$7</span></div>
  <div class="card c2" style="top:244px"><div class="shot" role="img" aria-label="Tray of basmati rice"></div><span class="name">BASMATI RICE</span><span class="size">16OZ</span><span class="price">$7</span></div>
  <div class="card c3" style="top:244px"><div class="shot" role="img" aria-label="Tray of quinoa"></div><span class="name">QUINOA</span><span class="size">16OZ</span><span class="price">$7</span></div>
  <div class="card c1" style="top:306px"><div class="shot" role="img" aria-label="Tray of pesto pasta"></div><span class="name">PESTO PASTA</span><span class="size">16OZ</span><span class="price">$9.50</span></div>
</section>

<section class="page back">
  <div class="photo main" role="img" aria-label="Salad bowl, asparagus and a creamy shrimp pasta dish on a wooden table"></div>
  <div class="addr a1">Healthy Kitchen | Heron Flats<br>Unit 17-135 Heron Flats Blvd,<br>Tamarack Falls AB, T0X 1A1</div>
  <div class="addr a2">Healthy Kitchen | Wren Crescent<br>Unit 110-2107 Linden Avenue,<br>Brookmoor AB, T0Y 2B2</div>
  <div class="social ig"><span class="mark"></span>ploverbarnkitchen</div>
  <div class="social fb"><span class="mark"></span>Plover Barn Healthy Kitchen &amp; Meal Prep</div>
  <div class="photo strip" role="img" aria-label="Edge of food photograph"></div>
</section>

</body>
</html>
```